E-Book-Cover für Ratgeber zum Thema Weisheit
Zielgruppe
Ich bin ein experimenteller Schriftsteller, der ein E-Book über Quellbuch Verlagsdienst auf Buchora veröffentlichen möchte. Das Thema des Ratgebers ist Weisheit.
Weisheit gilt als ein eher antiquierter und abstrakter Begriff. Das ist ein Irrtum. Sie ist wichtiger als je zuvor und kann beschrieben werden. Weder ist sie gleichzusetzen mit Klugheit, noch mit spiritueller Erleuchtung. Sie beinhaltet bestimmte Eigenschaften wie Vernunft, Wissbegierde, Demut, Einfühlungsvermögen, Intuition, Auflehnung... Wobei rationales Denken das oberste Gebot ist. Es wird u.a. gezeigt, was Weisheit für das eigene Leben bringt und wie man sie anstreben kann.
Die Zielgruppe sind alle Menschen, die an Philosophie, Psychologie, Selbstoptimierung oder Religionen bzw. Atheismus interessiert sind. Menschen, die nach einer Erkenntnis oder 'Erleuchtung' suchen und etwas Besonderes in der Bücherflut entdecken möchten. Es ist weniger für Akademiker geschrieben; eher für die 'normale', durchschnittliche Bevölkerung und kann auch von bildungsferneren Schichten aller Altersgruppen verstanden werden.
Meine Vermutung ist, dass es bei offenen Personen mittleren Alters Anklang finden könnte.
Aufgabenstellung
Der Titel und der Untertitel des Buches müssen vorkommen (Titel: 'Der Klare Blick'; Untertitel: 'Wie Sie mit dem revolutionären Konzept der modernen Weisheit wahre Größe erlangen'). Außerdem soll ein runder Button/Aufkleber/Sticker auf dem Cover kleben, welcher folgenden Text enthält: 'Mit Selbsttest! Wie weise bin ich?').
Natürlich soll der Name des Autors ebenfalls vorkommen: 'Malte Ruhland'
Das Cover soll sehr aus der Masse herausstechen, demnach ein echter Hingucker sein. Der potenzielle Kunde soll sofort neugierig sein! Es muss sowohl klein (als Thumbnail und am Smartphone), als auch groß gut aussehen und der Titel stets gut lesbar sein. Außerdem muss es schwarzweiß gut aussehen und erkennbar sein (für ebook-reader).
Buchora gibt folgende Werte für die Bilddatei vor: Die idealen Abmessungen für Coverdateien liegen bei 2 560 x 1 600 Pixeln. Mindestens 300 dpi. Die Größe der Bilddatei sollte 50MB nicht übersteigen. Farbprofil: RGB. DATEIFORMAT: JPG oder TIFF
Coverbilder mit weißem oder sehr hellem Hintergrund heben sich kaum vom Hintergrund ab. Fügen Sie einen dünnen Rahmen (3–4 Pixel) in Mittelgrau hinzu, um die Ränder des Coverbilds besser sichtbar zu machen.
Welches Cover gut zum Thema Weisheit passt, überlasse ich Ihrer Genialität. Ich dachte vielleicht an eine Art Blitz, Supernova, Erleuchtung, Explosion, geometrische Form o.ä. Aber Sie können sich etwas ganz eigenes ausdenken. Es sollte eher abstrakt sein. Außerdem muss es klar, edel und modern wirken, weniger comichaft oder verspielt/kitschig. Es darf etwas aggressiv bzw. 'revolutionär' wirken.

```html
<!DOCTYPE html>
<html lang="de">
<head>
<meta charset="utf-8">
<title>Der Klare Blick – Malte Ruhland</title>
<link href="https://fonts.googleapis.com/css2?family=Orbitron:wght@500;600&family=Open+Sans:wght@700&display=swap" rel="stylesheet">
<style>
  :root {
    --night: #1c2637;
    --navy: #2e3d57;
    --steel: #5b7196;
    --haze: #a9bcd8;
    --glow: #f4f8ff;
    --white: #ffffff;
    --band: rgba(170, 180, 196, 0.55);
    --sticker: rgba(150, 164, 188, 0.78);
  }
  html, body {
    margin: 0;
    padding: 0;
    overflow: hidden;
    background: var(--night);
  }
  .cover {
    position: relative;
    width: 750px;
    height: 1200px;
    overflow: hidden;
    font-family: "Open Sans", "Calibri", sans-serif;
    font-weight: 700;
    color: var(--white);
  }
  .cover__scene {
    position: absolute;
    inset: 0;
    background:
      radial-gradient(ellipse 90px 300px at 355px 750px, var(--glow) 0%, rgba(220,232,250,0.85) 40%, rgba(169,188,216,0) 100%),
      radial-gradient(ellipse 260px 420px at 380px 820px, rgba(169,188,216,0.75) 0%, rgba(91,113,150,0.25) 60%, rgba(91,113,150,0) 100%),
      linear-gradient(180deg, var(--night) 0%, var(--navy) 35%, #4a5e80 70%, var(--steel) 100%);
  }
  .cover__author {
    position: absolute;
    top: 46px;
    left: 0;
    width: 100%;
    text-align: center;
    font-family: "Orbitron", sans-serif;
    font-weight: 500;
    font-size: 41px;
    letter-spacing: 1px;
    line-height: 1;
  }
  .cover__title {
    position: absolute;
    top: 120px;
    left: 0;
    width: 100%;
    margin: 0;
    text-align: center;
    font-family: "Orbitron", sans-serif;
    font-weight: 600;
    font-size: 100px;
    line-height: 148px;
    letter-spacing: 0;
    white-space: nowrap;
  }
  .cover__sticker {
    position: absolute;
    top: 410px;
    left: 520px;
    width: 212px;
    height: 212px;
  }
  .cover__sticker svg {
    position: absolute;
    inset: 0;
  }
  .cover__sticker-text {
    position: absolute;
    inset: 0;
    display: flex;
    align-items: center;
    justify-content: center;
    text-align: center;
    font-size: 25px;
    line-height: 32px;
  }
  .cover__subtitle {
    position: absolute;
    top: 1050px;
    left: 0;
    width: 750px;
    height: 114px;
  }
  .cover__subtitle svg {
    position: absolute;
    inset: 0;
  }
  .cover__subtitle-text {
    position: absolute;
    top: 6px;
    left: 40px;
    right: 0;
    margin: 0;
    text-align: center;
    font-size: 28px;
    line-height: 42px;
    letter-spacing: -0.3px;
    text-transform: uppercase;
    text-shadow: 1px 2px 3px rgba(20, 28, 42, 0.6);
    white-space: nowrap;
  }
</style>
</head>
<body>
  <main class="cover">
    <div class="cover__scene" role="img" aria-label="Dunkler bläulicher Raum mit halb geöffneter Tür, durch die helles Licht hereinfällt"></div>

    <div class="cover__author">MALTE RUHLAND</div>

    <h1 class="cover__title">DER KLARE<br>BLICK</h1>

    <div class="cover__sticker">
      <svg width="212" height="212" viewBox="0 0 212 212" aria-hidden="true">
        <circle cx="106" cy="106" r="104" fill="var(--sticker)"/>
        <circle cx="106" cy="106" r="95" fill="none" stroke="var(--white)" stroke-opacity="0.55" stroke-width="2"/>
      </svg>
      <div class="cover__sticker-text">Mit Selbsttest!<br>Wie weise<br>bin ich?</div>
    </div>

    <div class="cover__subtitle">
      <svg width="750" height="114" viewBox="0 0 750 114" aria-hidden="true">
        <polygon points="70,0 672,0 720,114 23,114" fill="var(--band)" opacity="0.7"/>
      </svg>
      <p class="cover__subtitle-text">Wie Sie mit dem revolutionären Konzept<br>der modernen Weisheit<br>wahre Grösse erlangen</p>
    </div>
  </main>
</body>
</html>
```